To design a look and feel for a website. The company offers technical services to governemtns and public bodies. It does NOT market to the public.

The core business is GIS (Geographic Information Systems)

The site needs to be clean and simple, The current version is available here: www.velda-maps.ie

Thanks for your interest in our project

Target Market(s)

Goverment agencies and public bodies in the EU, buying through the public procurerment process

Requirements
Should not have
• corny graphics of hands holding globes or sateliites please.

```html
<!DOCTYPE html>
<html lang="en">
<head>
<meta charset="utf-8">
<title>The VELDA Group – Information Expertise</title>
<link href="https://fonts.googleapis.com/css2?family=Roboto:ital,wght@0,300;0,400;0,500;0,700;1,400;1,500&family=Noticia+Text:wght@700&display=swap" rel="stylesheet">
<style>
:root{
  --navy:#223f7a;
  --navy-footer:#233f7c;
  --blue-text:#2b4a8b;
  --lilac:#7b7bbf;
  --lilac-bar:#7d7cb8;
  --ink:#333;
  --muted:#666;
  --page:#f2f2f2;
  --header:#fafafa;
  --rule:#c9c9c9;
}
*{margin:0;padding:0;box-sizing:border-box}
html,body{width:1167px;height:1200px;overflow:hidden}
body{position:relative;font-family:"Roboto",sans-serif;color:var(--ink);background:var(--page)}
a{color:inherit;text-decoration:none}
.abs{position:absolute}

/* top bar */
.topbar{position:absolute;left:0;top:0;width:1167px;height:28px;background:var(--navy)}
.search{position:absolute;left:707px;top:5px;width:193px;height:19px;background:#fff;border:1px solid #ccc;font:italic 10px "Roboto",sans-serif;color:#888;padding:3px 6px}
.search svg{position:absolute;right:6px;top:4px}
.topbar-contact{position:absolute;left:915px;top:0;width:87px;height:28px;background:var(--lilac);color:#fff;font-weight:500;font-size:11.5px;text-align:center;line-height:29px}

/* header */
.header{position:absolute;left:0;top:28px;width:1167px;height:136px;background:var(--header)}
.brand{position:absolute;left:168px;top:52px;display:flex;align-items:center;gap:8px;color:var(--blue-text);font-weight:500;font-size:27px;letter-spacing:.5px}
.brand-dot{width:10px;height:10px;border-radius:50%;background:var(--lilac)}
.brand-tag{position:absolute;left:168px;top:92px;font-size:13px;font-weight:300;color:var(--lilac)}
.nav-item{position:absolute;top:92px;width:90px;margin-left:-45px;text-align:center;font-size:12.5px;font-weight:500;color:#222}
.nav-item svg{display:block;margin:0 auto 6px}
.nav-item.active{color:var(--blue-text)}
.nav-sep{position:absolute;top:92px;width:1px;height:58px;background:#e0e0e0}
.nav-underline{position:absolute;left:362px;top:161px;width:61px;height:3px;background:var(--navy)}
.call{position:absolute;left:809px;top:100px;width:193px;height:42px;background:var(--lilac);color:#fff;font-size:15px;display:flex;align-items:center;justify-content:center;gap:8px;border-radius:2px}
.call b{font-weight:500}

/* hero */
.hero{position:absolute;left:0;top:164px;width:1167px;height:412px;background:linear-gradient(180deg,#8d9196 0%,#b9bcbf 40%,#9ea3a6 100%)}
.hero-screen{position:absolute;left:270px;top:0;width:600px;height:330px;background:linear-gradient(135deg,#3a3a3a,#1c1c1c);border-radius:0 0 18px 18px}
.hero-screen::after{content:"";position:absolute;left:50px;top:18px;width:490px;height:300px;background:linear-gradient(135deg,#c9d0c5,#9fc35a 50%,#5b93c9)}
.hero-arrow{position:absolute;top:322px;width:44px;height:44px;border-radius:50%;background:rgba(60,60,60,.55);display:flex;align-items:center;justify-content:center}
.hero-caption{position:absolute;left:0;top:330px;width:1167px;height:82px;background:rgba(40,40,40,.6);color:#fff;font-family:"Noticia Text",serif;font-weight:700;font-size:24.5px;line-height:36px;text-align:center;padding-top:9px;text-shadow:0 1px 2px rgba(0,0,0,.5)}

/* intro columns */
.col{position:absolute;top:612px}
.col h2{font-weight:300;font-size:21.5px;color:#444;padding-bottom:8px;border-bottom:1px solid var(--rule)}
.col h2 span{color:var(--blue-text)}
.col p{font-size:11.7px;line-height:17px;letter-spacing:.4px;margin-top:14px;color:#333}
.checks{list-style:none;margin-top:5px}
.checks li{font-size:12.3px;line-height:19px;display:flex;align-items:center;gap:6px}
.more{position:absolute;top:798px;font-style:italic;font-weight:500;font-size:11px;color:var(--blue-text);text-decoration:underline}
.news{position:absolute;left:771px;display:flex;gap:10px}
.date{width:37px;height:37px;text-align:center;flex:none}
.date-m{background:var(--lilac);color:#fff;font-size:10px;font-weight:500;height:14px;line-height:15px}
.date-d{background:var(--navy);color:#fff;font-size:14px;font-weight:500;height:23px;line-height:23px}
.news p{font-size:10.5px;line-height:16.5px;color:#666;letter-spacing:.5px;width:186px;margin-top:-2px}

/* clients */
.dash{position:absolute;left:167px;width:835px;border-top:2px dotted #c4c4c4}
.clients-label{position:absolute;left:169px;top:886px;font-style:italic;font-size:17px;color:#555}
.client{position:absolute;top:861px;height:64px;display:flex;align-items:center;justify-content:center;gap:7px;font-size:17px;font-weight:500;color:var(--navy)}
.client i{width:14px;height:14px;border-radius:50%;background:var(--lilac);display:block}

/* footer */
.footer{position:absolute;left:0;top:983px;width:1167px;height:174px;background:var(--navy-footer);color:#fff}
.f-head{position:absolute;top:18px;display:flex;align-items:center;gap:7px;font-size:17px;font-weight:300}
.f-list{position:absolute;list-style:none}
.f-list li{display:flex;align-items:center;gap:8px}
.f-list li::before{content:"";width:5px;height:5px;background:#fff;display:block}
.f-sep{position:absolute;top:17px;width:1px;height:134px;background:rgba(255,255,255,.25)}
.f-note{position:absolute;left:539px;top:62px;font-size:11.5px;line-height:16px;width:200px}
.f-input{position:absolute;left:539px;top:96px;width:185px;height:24px;background:#fff;border-radius:2px;color:#666;font:italic 10px "Roboto",sans-serif;padding:6px 8px}
.f-btn{position:absolute;left:539px;top:129px;width:101px;height:25px;background:var(--lilac);border-radius:2px;font-size:12.5px;font-weight:700;text-align:center;line-height:25px}
.f-brand{position:absolute;left:842px;top:46px;display:flex;align-items:center;gap:8px;font-size:27px;font-weight:500}
.f-brand i{width:10px;height:10px;border-radius:50%;background:#fff;display:block}
.f-tag{position:absolute;left:842px;top:86px;font-size:13px;font-weight:300}
.bottom{position:absolute;left:0;top:1157px;width:1167px;height:43px;background:var(--lilac-bar);color:#fff;font-size:12px;text-align:center;line-height:43px}
</style>
</head>
<body>

<div class="topbar">
  <div class="search">Type Word...
    <svg width="10" height="10" viewBox="0 0 10 10"><circle cx="4" cy="4" r="3" fill="none" stroke="#999" stroke-width="1.4"/><path d="M6.2 6.2 9 9" stroke="#999" stroke-width="1.6"/></svg>
  </div>
  <a class="topbar-contact" href="#">CONTACT US</a>
</div>

<header class="header">
  <div class="brand" style="top:24px"><span>The VELDA Group</span><i class="brand-dot"></i></div>
  <div class="brand-tag" style="top:64px">Information Expertise</div>

  <a class="nav-item active" href="#" style="left:392px;top:64px">
    <svg width="26" height="26" viewBox="0 0 24 24"><path d="M12 3 2 12h3v8h5v-5h4v5h5v-8h3z" fill="#333"/></svg>HOME</a>
  <span class="nav-sep" style="left:428px;top:64px"></span>
  <a class="nav-item" href="#" style="left:477px;top:60px">
    <svg width="30" height="30" viewBox="0 0 30 30"><circle cx="11" cy="11" r="6" fill="none" stroke="#444" stroke-width="3" stroke-dasharray="3 2"/><circle cx="20" cy="20" r="5" fill="none" stroke="#444" stroke-width="3" stroke-dasharray="3 2"/></svg>SERVICES</a>
  <span class="nav-sep" style="left:523px;top:64px"></span>
  <a class="nav-item" href="#" style="left:568px;top:64px">
    <svg width="34" height="26" viewBox="0 0 34 26"><circle cx="11" cy="7" r="5" fill="#222"/><circle cx="22" cy="6" r="5" fill="#222"/><path d="M2 24c0-7 4-10 9-10s9 3 9 10zM14 22c1-7 4-9 8-9s9 3 9 9z" fill="#222"/></svg>CLIENTS</a>
  <span class="nav-sep" style="left:609px;top:64px"></span>
  <a class="nav-item" href="#" style="left:658px;top:64px">
    <svg width="26" height="26" viewBox="0 0 26 26"><circle cx="13" cy="13" r="11.5" fill="none" stroke="#222" stroke-width="2"/><path d="M9 7c-2 2 0 7 3 10s7 4 8 2l-2-2-2 1c-2-1-4-3-5-5l1-2z" fill="#222"/></svg>CONTACT</a>
  <span class="nav-sep" style="left:705px;top:64px"></span>
  <a class="nav-item" href="#" style="left:749px;top:64px">
    <svg width="28" height="26" viewBox="0 0 28 26"><circle cx="14" cy="12" r="6" fill="none" stroke="#333" stroke-width="1.8"/><path d="M11 19h6M12 22h4M14 1v3M4 5l2 2M24 5l-2 2M1 12h3M24 12h3" stroke="#333" stroke-width="1.6"/></svg>INSPIRE</a>
  <span class="nav-underline" style="top:133px"></span>

  <a class="call" href="#" style="top:72px">
    <svg width="14" height="14" viewBox="0 0 14 14"><path d="M3 1c-2 1-2 4 1 7s6 4 8 2l-2-3-2 1c-1-1-2-2-3-3l1-2z" fill="#fff"/></svg>
    <span>Call :<b>+ 353 1 555 0142</b></span></a>
</header>

<section class="hero" role="img" aria-label="Photograph of a tablet showing a city map with location pins, surrounded by model skyscrapers">
  <div class="hero-screen"></div>
  <span class="hero-arrow" style="left:11px"><svg width="14" height="20" viewBox="0 0 14 20"><path d="M11 2 3 10l8 8" fill="none" stroke="#fff" stroke-width="2.4"/></svg></span>
  <span class="hero-arrow" style="left:1100px"><svg width="14" height="20" viewBox="0 0 14 20"><path d="M3 2l8 8-8 8" fill="none" stroke="#fff" stroke-width="2.4"/></svg></span>
  <div class="hero-caption">As Ireland's Largest Satelite Image Processer, We Can Provide You With<br>Background Imagery For Your Project...</div>
</section>

<section class="col" style="left:168px;width:266px">
  <h2>About <span>The VELDA Group</span></h2>
  <p>The VELDA Group has been in business since 1994 and continues to develop and update its range of services. The company has a high level of expertise in handling data and information, and in building and re-engineering database systems. We have a particular expertise in working with Irish data sets and have a strong grounding in dealing with spatial data.</p>
</section>
<a class="more" href="#" style="left:361px">Read More &gt;&gt;</a>

<section class="col" style="left:486px;width:251px">
  <h2>Services <span>We Provide</span></h2>
  <p>VELDA has extensive experience in Spatial Data processing. Services include:</p>
  <ul class="checks">
    <li><svg width="13" height="9" viewBox="0 0 13 9"><path d="M1 4l4 4 7-7" fill="none" stroke="#2b4a8b" stroke-width="2"/></svg>Data Management</li>
    <li><svg width="13" height="9" viewBox="0 0 13 9"><path d="M1 4l4 4 7-7" fill="none" stroke="#2b4a8b" stroke-width="2"/></svg>Spatial Data</li>
    <li><svg width="13" height="9" viewBox="0 0 13 9"><path d="M1 4l4 4 7-7" fill="none" stroke="#2b4a8b" stroke-width="2"/></svg>Land Use</li>
    <li><svg width="13" height="9" viewBox="0 0 13 9"><path d="M1 4l4 4 7-7" fill="none" stroke="#2b4a8b" stroke-width="2"/></svg>Transport</li>
    <li><svg width="13" height="9" viewBox="0 0 13 9"><path d="M1 4l4 4 7-7" fill="none" stroke="#2b4a8b" stroke-width="2"/></svg>Consulting</li>
  </ul>
</section>
<a class="more" href="#" style="left:652px">Read More &gt;&gt;</a>

<section class="col" style="left:771px;width:231px">
  <h2>Latest <span>News</span></h2>
</section>
<div class="news" style="top:661px"><div class="date"><div class="date-m">DEC</div><div class="date-d">22</div></div><p>Lorem ipsum dolor sit Lorem amet consectetuer adipiscing elit, sed diam nonummy...</p></div>
<div class="news" style="top:727px"><div class="date"><div class="date-m">DEC</div><div class="date-d">23</div></div><p>Lorem ipsum dolor sit Lorem amet consectetuer adipiscing elit, sed diam nonummy...</p></div>
<a class="more" href="#" style="left:937px">View All &gt;&gt;</a>

<div class="dash" style="top:838px"></div>
<div class="clients-label">Our Clients :</div>
<svg class="abs" style="left:291px;top:887px" width="14" height="20" viewBox="0 0 14 20"><path d="M11 2 3 10l8 8" fill="none" stroke="#888" stroke-width="2"/></svg>
<div class="client" style="left:318px;width:105px"><i></i>Harbour Survey</div>
<div class="client" style="left:451px;width:167px">Coach Link</div>
<div class="client" style="left:644px;width:229px"><i></i>Metro Transit</div>
<div class="client" style="left:892px;width:90px;font-size:14px">Global Assembly</div>
<svg class="abs" style="left:987px;top:887px" width="14" height="20" viewBox="0 0 14 20"><path d="M3 2l8 8-8 8" fill="none" stroke="#888" stroke-width="2"/></svg>
<div class="dash" style="top:949px"></div>

<footer class="footer">
  <div class="f-head" style="left:167px"><svg width="17" height="22" viewBox="0 0 17 22"><rect x="1" y="3" width="15" height="18" fill="none" stroke="#fff" stroke-width="1.5"/><rect x="5" y="1" width="7" height="4" fill="#fff"/><path d="M4 10h9M4 14h9M4 18h6" stroke="#fff"/></svg>Main Menu</div>
  <ul class="f-list" style="left:167px;top:61px;font-size:12px;line-height:20.4px">
    <li>Home</li><li>Services</li><li>Clients</li><li>Contact</li><li>Inspire</li>
  </ul>
  <span class="f-sep" style="left:311px"></span>

  <div class="f-head" style="left:347px"><svg width="16" height="26" viewBox="0 0 16 26"><circle cx="6" cy="6" r="5" fill="none" stroke="#fff" stroke-width="1.3"/><path d="M5 6v10l-2-2-1 1 4 7h7l1-8-7-2V6z" fill="#fff"/></svg>Get In Touch</div>
  <ul class="f-list" style="left:353px;top:61px;font-size:12.5px;line-height:27px">
    <li>Community</li><li>Updates</li><li>Circles</li><li>Network</li>
  </ul>
  <span class="f-sep" style="left:502px"></span>

  <div class="f-head" style="left:539px"><svg width="36" height="26" viewBox="0 0 36 26"><path d="M2 10 28 2l6 16-26 8z" fill="none" stroke="#fff" stroke-width="1.6"/><path d="M2 10l16 6 10-14" fill="none" stroke="#fff" stroke-width="1.4"/></svg>Subscribe to Newsletter</div>
  <div class="f-note">get latest updates by entering your email address</div>
  <div class="f-input">Email Address</div>
  <a class="f-btn" href="#">Subscribe</a>
  <span class="f-sep" style="left:805px"></span>

  <div class="f-brand"><span>The VELDA Group</span><i></i></div>
  <div class="f-tag">Information Expertise</div>
</footer>
<div class="bottom">©2013The VELDA Group . All rights reserved.</div>

</body>
</html>
```